Simple and Clean business card design

We would like the design to be simple clean and to incorporate our colors.

We are open to your design and talent, we have the dots in our logo as we think of it as data points and we connect data points for people.

We are open to see the great creative and clean design you bring to the table

Contact Information for Business Card

please include: name, position, email, phone and website

Font styles to use
Sans Serif

Requirements
Must have
• my colors incorporated, simplicity
Nice to have
• lots of white space, simplicity
Should not have
• complexicity/ complex art

```html
<!DOCTYPE html>
<html lang="en">
<head>
<meta charset="utf-8">
<title>Nectra Business Card</title>
<link rel="stylesheet" href="https://fonts.googleapis.com/css2?family=Lato:wght@400;700&display=swap">
<style>
  :root {
    --backdrop: #a3a3a3;
    --card-dark: #131313;
    --card-light: #ffffff;
    --ink: #111111;
    --brand-blue: #4a86f0;
    --brand-green: #34a853;
    --brand-yellow: #fbbc05;
    --brand-red: #ea4335;
    --rule: #555555;
  }
  * { margin: 0; padding: 0; box-sizing: border-box; }
  html, body {
    width: 1200px; height: 1200px; overflow: hidden;
    background: var(--backdrop);
    font-family: "Lato", Arial, sans-serif;
  }
  .canvas { position: relative; width: 1200px; height: 1200px; }
  .card {
    position: absolute; width: 366px; height: 592px;
    border-radius: 14px;
    box-shadow: 2px 4px 6px rgba(0,0,0,0.35);
  }
  .card-front { left: 200px; top: 303px; background: var(--card-dark); }
  .card-back { left: 600px; top: 305px; background: var(--card-light); }

  .wordmark {
    position: absolute; left: 0; right: 0;
    display: flex; align-items: center; justify-content: center; gap: 12px;
    font-weight: 700; font-size: 74px; letter-spacing: 1px; line-height: 1;
  }
  .wordmark-dot { width: 18px; height: 18px; border-radius: 50%; background: var(--brand-blue); }
  .card-front .wordmark { top: 472px; color: var(--card-light); }
  .card-back .wordmark { top: 140px; color: var(--ink); }

  .contact {
    position: absolute; left: 0; right: 0; top: 380px;
    text-align: center; color: var(--ink);
  }
  .person-name { font-weight: 700; font-size: 27px; color: var(--brand-blue); letter-spacing: 0.3px; }
  .person-role { font-size: 17px; margin-top: 1px; }
  .icon-row {
    display: flex; align-items: center; justify-content: center; gap: 4px;
    margin: 12px 0 8px;
  }
  .icon-rule { width: 22px; height: 1px; background: var(--rule); margin: 0 3px; }
  .icon { width: 25px; height: 25px; }
  .contact-line { font-size: 16px; line-height: 25px; }
</style>
</head>
<body>
<main class="canvas">
  <section class="card card-front">
    <div class="wordmark"><span class="wordmark-dot"></span>Nectra</div>
  </section>

  <section class="card card-back">
    <div class="wordmark"><span class="wordmark-dot"></span>Nectra</div>

    <div class="contact">
      <div class="person-name">DANIEL MOSS</div>
      <div class="person-role">Founder/ CEO</div>

      <div class="icon-row">
        <span class="icon-rule"></span>
        <svg class="icon" viewBox="0 0 26 26" aria-label="Phone">
          <circle cx="13" cy="13" r="13" fill="var(--brand-green)"/>
          <path d="M9 7.5c.6-.5 1.4-.4 1.8.2l1 1.6c.3.5.2 1.1-.2 1.5l-.7.6c.6 1.4 1.6 2.5 3 3.1l.6-.7c.4-.4 1-.5 1.5-.2l1.6 1c.6.4.7 1.2.2 1.8l-.6.7c-.6.6-1.5.8-2.3.5-2.9-1.2-5.2-3.5-6.4-6.4-.3-.8-.1-1.7.5-2.3z" fill="#fff"/>
        </svg>
        <svg class="icon" viewBox="0 0 26 26" aria-label="Email">
          <circle cx="13" cy="13" r="13" fill="var(--brand-yellow)"/>
          <rect x="7" y="9" width="12" height="8.5" rx="0.8" fill="none" stroke="#fff" stroke-width="1.4"/>
          <path d="M7.3 9.4 13 14l5.7-4.6" fill="none" stroke="#fff" stroke-width="1.4"/>
        </svg>
        <svg class="icon" viewBox="0 0 26 26" aria-label="Website">
          <circle cx="13" cy="13" r="13" fill="var(--brand-red)"/>
          <g fill="none" stroke="#fff" stroke-width="1.2">
            <circle cx="13" cy="13" r="6"/>
            <ellipse cx="13" cy="13" rx="2.6" ry="6"/>
            <path d="M7 13h12M8 10h10M8 16h10"/>
          </g>
        </svg>
        <span class="icon-rule"></span>
      </div>

      <div class="contact-line">780-555-0142</div>
      <div class="contact-line">daniel.moss@nectra.one</div>
      <div class="contact-line">www.Nectra.one</div>
    </div>
  </section>
</main>
</body>
</html>
```